Modern Business Card

Modern professional business card with more than just logo and demographic info. Something memorable.

We are a trendy/modern chiropractic group with an emphasis on neurology, hence the minimalist-type brain logo. We want to convey that modern and technical aspect with professionalism and the elite nature of our practice environment.

```html
<!DOCTYPE html>
<html lang="en">
<head>
<meta charset="utf-8">
<title>Meridian Chiropractic – Business Card</title>
<link href="https://fonts.googleapis.com/css2?family=Cinzel:wght@400&family=Lato:wght@400&family=Arimo:wght@700&display=swap" rel="stylesheet">
<style>
  :root {
    --page-bg: #e9e7e4;
    --card-top: #fbfbfb;
    --ink-dark: #1c1c1c;
    --brand-blue: #3f7fd0;
    --band-black: #0b0b0c;
    --band-grey: #5a5a5c;
    --text-light: #e6e6e6;
    --text-soft: #d0d0d0;
  }
  * { box-sizing: border-box; margin: 0; padding: 0; }
  html, body {
    width: 1200px; height: 900px; overflow: hidden;
    background: var(--page-bg);
  }
  .canvas {
    width: 1200px; height: 900px;
    display: flex; align-items: center; justify-content: center;
  }
  .business-card {
    width: 960px; height: 596px;
    display: flex; flex-direction: column;
    box-shadow: 0 18px 40px rgba(0,0,0,.18);
    font-family: "Lato", sans-serif;
  }
  .card-top {
    height: 326px; background: var(--card-top);
    display: flex; align-items: center; justify-content: center;
    padding-top: 8px;
  }
  .brand-lockup { display: flex; align-items: center; gap: 26px; }
  .brand-mark {
    width: 44px; height: 44px; background: var(--brand-blue);
  }
  .brand-name {
    font-family: "Cinzel", serif; font-weight: 400;
    color: var(--ink-dark); line-height: 1; text-transform: uppercase;
    display: flex; flex-direction: column;
  }
  .brand-name__primary { font-size: 66px; letter-spacing: 1px; }
  .brand-name__secondary { font-size: 36px; letter-spacing: 1px; margin-top: 4px; }
  .accent-rule { height: 6px; background: var(--brand-blue); }
  .card-band {
    flex: 1;
    background: linear-gradient(90deg, var(--band-black) 0%, var(--band-black) 46%, var(--band-grey) 46%, var(--band-grey) 100%);
    display: flex; justify-content: space-between;
    padding: 30px 44px 0 53px;
  }
  .person-name {
    font-family: "Arimo", sans-serif; font-weight: 700;
    color: var(--brand-blue); font-size: 34px; letter-spacing: .5px; line-height: 1.1;
  }
  .person-title { color: var(--text-light); font-size: 27px; margin-top: 4px; }
  .address {
    font-style: normal; color: var(--text-soft);
    font-size: 27px; line-height: 36px; margin-top: 24px;
  }
  .contact-list {
    list-style: none; text-align: right;
    color: var(--text-light); font-size: 27px; line-height: 35px;
    margin-top: 104px;
  }
  .contact-list li { display: flex; align-items: center; justify-content: flex-end; gap: 6px; }
  .contact-icon { width: 20px; height: 20px; fill: var(--text-light); }
</style>
</head>
<body>
<main class="canvas">
  <article class="business-card">
    <header class="card-top">
      <div class="brand-lockup">
        <span class="brand-mark" aria-hidden="true"></span>
        <h1 class="brand-name">
          <span class="brand-name__primary">Meridian</span>
          <span class="brand-name__secondary">Chiropractic</span>
        </h1>
      </div>
    </header>
    <div class="accent-rule"></div>
    <section class="card-band">
      <div class="identity">
        <h2 class="person-name">DANIEL CARTER</h2>
        <p class="person-title">Managing Director</p>
        <address class="address">214 Kestrel Road<br>Suite 12<br>30417,Westvale</address>
      </div>
      <ul class="contact-list">
        <li>044-555 218 640
          <svg class="contact-icon" viewBox="0 0 20 20" aria-hidden="true"><path d="M2 7c0-2 3-4 8-4s8 2 8 4v1h-4V6.5c-1-.6-2.5-.8-4-.8s-3 .2-4 .8V8H2z"/><path d="M5 9h10l2 7H3z"/></svg></li>
        <li>hello@meridianchiro.com
          <svg class="contact-icon" viewBox="0 0 20 20" aria-hidden="true"><path d="M2 4h16v12H2z M3.5 5.5 10 11l6.5-5.5" stroke="#5a5a5c" stroke-width="1.4"/></svg></li>
        <li>www.meridianchiro.com
          <svg class="contact-icon" viewBox="0 0 20 20" aria-hidden="true"><circle cx="10" cy="10" r="8"/><path d="M6 6c2 1 3 0 4 2s-1 3 1 5M12 4c1 2 3 2 4 4" stroke="#5a5a5c" stroke-width="1.5" fill="none"/></svg></li>
      </ul>
    </section>
  </article>
</main>
</body>
</html>
```